Belvascotravel.com web design project + logo design

Hi,

We are a Russian online tour operator - sunkettle.com

We are looking to tranmsfer our domain to belvascotravel.com. The website and logo need to be belvascoesque - we are not looking to change our functionality, but we need to make the website much more attracitve to clients, much more wild looking but at the same time remaining a professional travel company.

The main concept of the website should be innovative travel (as belvasco was an innovator). Alternatively, you could go down the artist route and go down the draw / design your own tour road.

On our website the customer is able to combine travel services (hotels, flights, Visa services, and soon chauffeur, car rental etc...) put it into their basket (the basket definitely has to look better than it is at the moment) and pay for it in one go by card.

We are also stressin our customer support with web chat, call centre etc... (call centre number at the top of the page)

We aim to provide an easy user experience, but we need to make it have some more style, so I will be waiting for what you guys can come up with.
Let me know if you have any questions - skype is: mrdolbarin

Industry/Entity Type

It Company

Requirements
Must have
• It is quite a simple task - to take the existing website sunkettle.com and belvascosize it to create belvascotravel.com, the functionality of the website will remain the same and there are not many pages in the website. Homepage, Checkout step1, Checkout step 2 (you can view both of these if you select a service) and the generic pages for T&C''s, Privacy policy etc...

IMPORTANT UPDATE

We are also looking at how the search results will look in the designs, (please do a search on our website for hotel / flight)

```html
<!DOCTYPE html>
<html lang="ru">
<head>
<meta charset="utf-8">
<title>Belvasco Travel — Ваш заказ</title>
<link rel="stylesheet" href="https://fonts.googleapis.com/css2?family=PT+Sans:wght@400;700&family=PT+Sans+Narrow&family=PT+Serif:wght@400;700&display=swap">
<style>
  :root {
    --paper: #efeadb;
    --paper-light: #f4f0e4;
    --ink: #2b140a;
    --ink-soft: #4a2a1a;
    --rust: #6b2310;
    --link: #7a1a0a;
    --night: #2a1208;
    --field: #ffffff;
    --mail-field: #ddd6b8;
    --rule: #c9bfa5;
  }
  * { box-sizing: border-box; margin: 0; padding: 0; }
  html, body { width: 1024px; height: 1200px; overflow: hidden; }
  body {
    position: relative;
    background: var(--paper);
    color: var(--ink);
    font-family: "PT Sans", Arial, sans-serif;
  }
  .abs { position: absolute; }

  /* header */
  .site-header { position: absolute; left: 0; top: 0; width: 1024px; height: 130px; background: var(--paper-light); }
  .compass { position: absolute; left: -40px; top: -46px; width: 150px; height: 160px; border-radius: 50%;
    background: radial-gradient(circle, #e8dcc0 0%, #cdb690 55%, #8a5a30 70%, #5a3418 100%); }
  .phone-icon { left: 122px; top: 47px; }
  .phones { left: 168px; top: 46px; font-family: "PT Serif", Georgia, serif; font-size: 12.5px; line-height: 18px; color: var(--ink); }
  .brand { left: 412px; top: 26px; width: 200px; text-align: center; font-family: "PT Serif", Georgia, serif; color: var(--ink); }
  .brand-dot { display: block; width: 14px; height: 14px; border-radius: 50%; background: var(--ink); margin: 0 auto 4px; }
  .brand-name { font-size: 28px; letter-spacing: 0.5px; line-height: 30px; border-bottom: 1.5px solid var(--ink); display: inline-block; padding: 0 2px; }
  .brand-sub { font-size: 10px; letter-spacing: 5px; margin-top: 4px; }
  .top-nav { left: 708px; top: 54px; display: flex; align-items: center; font-family: "PT Serif", Georgia, serif; font-size: 11.5px; color: var(--ink); }
  .top-nav a { display: flex; align-items: center; gap: 7px; color: inherit; text-decoration: none; }
  .top-nav .sep { width: 1px; height: 20px; border-left: 1px dotted var(--rule); margin: 0 18px; }

  .hero { left: 0; top: 130px; width: 1024px; height: 219px;
    background: linear-gradient(180deg, #3a3c5a 0%, #a58a55 38%, #6a6042 58%, #2d2b3a 72%, #6a7784 100%); }

  /* order */
  .order-title { left: 0; top: 373px; width: 1024px; text-align: center; font-family: "PT Serif", Georgia, serif; font-size: 15px; letter-spacing: 0.5px; }
  .service-badge { left: 153px; top: 372px; width: 56px; height: 56px; border-radius: 50%; background: var(--rust); }
  .service-label { left: 131px; top: 435px; width: 100px; text-align: center; font-family: "PT Sans Narrow", sans-serif; font-size: 11.5px; color: var(--rust); }

  .steps { left: 288px; top: 417px; width: 589px; height: 34px; background: var(--night); display: flex; list-style: none; }
  .step { position: relative; height: 34px; display: flex; align-items: center; color: #f1e6d6; font-family: "PT Sans Narrow", sans-serif; font-size: 12px; letter-spacing: 0.3px; }
  .step b { font-family: "PT Serif", Georgia, serif; font-weight: 400; font-size: 17px; margin: 0 10px 0 0; }
  .step.active { background: var(--rust); }
  .step svg { position: absolute; right: -6px; top: 0; }

  .leg { font-size: 9.5px; color: var(--link); line-height: 16px; }
  .leg h3 { font-family: "PT Serif", Georgia, serif; font-weight: 400; font-size: 13px; color: var(--ink); margin-bottom: 6px; }
  .carrier { display: flex; align-items: center; gap: 6px; margin: 14px 0 14px; font-weight: 700; font-size: 12px; color: var(--ink); height: 20px; }
  .carrier i { width: 14px; height: 14px; border-radius: 50%; background: var(--ink); display: inline-block; }
  .leg dl { display: grid; grid-template-columns: 79px auto; }

  .terms { left: 157px; top: 659px; font-size: 11px; color: var(--ink); }
  .price-tag { left: 759px; top: 649px; width: 117px; height: 31px; background: var(--rust); color: #fff; font-family: "PT Serif", Georgia, serif; font-weight: 700; font-size: 15px; display: flex; align-items: center; justify-content: center; }

  .field-label { font-size: 11px; font-weight: 700; color: var(--ink); }
  .field { height: 31px; background: var(--field); }
  .select-arrow { position: absolute; right: 0; top: 0; width: 26px; height: 31px; border-left: 1px dotted #ccc; display: flex; align-items: center; justify-content: center; }
  .nodate { left: 786px; top: 791px; display: flex; align-items: center; gap: 9px; font-size: 11px; font-weight: 700; }
  .tick { width: 13px; height: 13px; border-radius: 3px; background: var(--night); display: flex; align-items: center; justify-content: center; }

  .nav-btn { top: 861px; font-family: "PT Serif", Georgia, serif; font-weight: 700; font-size: 15.5px; color: var(--ink); letter-spacing: 0.5px; }
  .total { left: 388px; top: 856px; width: 249px; height: 31px; background: var(--rust); color: #fff; font-family: "PT Serif", Georgia, serif; font-weight: 700; font-size: 15px; display: flex; align-items: center; justify-content: center; }

  /* footer */
  .foot-col { z-index: 2; }
  .foot-col h4 { font-family: "PT Serif", Georgia, serif; font-weight: 400; font-size: 12.5px; letter-spacing: 0.4px; color: var(--ink); margin-bottom: 16px; }
  .foot-col li { list-style: none; font-size: 9.5px; line-height: 17.3px; color: var(--ink); letter-spacing: 0.2px; }
  .social { left: 671px; top: 1028px; display: flex; gap: 11px; }
  .social span { width: 36px; height: 36px; border-radius: 50%; background: #e0d2b0; box-shadow: inset 0 0 0 2px #cdb994; }
  .contacts { left: 671px; top: 1079px; font-size: 9.5px; color: var(--ink); }
  .contacts li { list-style: none; display: flex; align-items: center; gap: 10px; height: 21px; }
  .contacts svg { width: 12px; }
  .mail-form { left: 672px; top: 1151px; display: flex; gap: 4px; }
  .mail-form .mail { width: 158px; height: 22px; background: var(--mail-field); font-size: 9.5px; color: #6b5a40; padding: 5px 9px; }
  .mail-form .send { width: 65px; height: 22px; background: var(--night); color: #fff; font-size: 9.5px; display: flex; align-items: center; justify-content: center; }
  .old-map { z-index: 1; left: 368px; top: 1112px; width: 212px; height: 120px; transform: rotate(8deg); background: linear-gradient(135deg, #e6d8b4, #b9a27a); box-shadow: 0 2px 6px rgba(0,0,0,.25); }
  .copyright { left: 122px; top: 1158px; font-size: 11px; color: var(--ink); }
</style>
</head>
<body>

<header class="site-header">
  <div class="compass" role="img" aria-label="Antique brass compass decoration"></div>
  <svg class="abs phone-icon" width="32" height="34" viewBox="0 0 32 34" aria-hidden="true">
    <path d="M2 10 Q16 0 30 10 L27 15 L22 13 L21 9 Q16 7 11 9 L10 13 L5 15 Z" fill="#2b140a"/>
    <path d="M8 17 L24 17 L29 32 L3 32 Z" fill="#2b140a"/>
    <circle cx="16" cy="24" r="4.5" fill="#f4f0e4"/>
    <circle cx="16" cy="24" r="2" fill="#2b140a"/>
  </svg>
  <div class="abs phones">+8 (800) 5550142<br>+7 (495) 5550187</div>

  <div class="abs brand">
    <span class="brand-dot"></span>
    <div class="brand-name">BELVASCO</div>
    <div class="brand-sub">TRAVEL</div>
  </div>

  <nav class="abs top-nav">
    <a href="#">
      <svg width="22" height="20" viewBox="0 0 22 20" aria-hidden="true"><path d="M11 1 C17 1 21 4.5 21 9 C21 13.5 17 17 11 17 L5 19 L6 15 C3 13.5 1 11.5 1 9 C1 4.5 5 1 11 1 Z" fill="#2b140a"/></svg>
      ФОРУМ
    </a>
    <span class="sep"></span>
    <a href="#">
      <svg width="20" height="20" viewBox="0 0 20 20" aria-hidden="true"><path d="M3 18 L3 3 L15 3 L12 7.5 L15 12 L5 12 L5 18 Z" fill="#2b140a"/></svg>
      МОЙ ТУР
    </a>
  </nav>
</header>

<div class="abs hero" role="img" aria-label="Panoramic photo of a river embankment with a cathedral, stone bridge and a tour boat"></div>

<main>
  <h1 class="abs order-title" style="font-weight:400">ВАШ ЗАКАЗ</h1>

  <div class="abs service-badge">
    <svg width="56" height="56" viewBox="0 0 56 56" aria-hidden="true">
      <g transform="rotate(-45 28 28)"><rect x="16" y="22" width="24" height="12" rx="1.5" fill="#fff"/><line x1="32" y1="22" x2="32" y2="34" stroke="#6b2310" stroke-width="1.5" stroke-dasharray="2 1.5"/></g>
    </svg>
  </div>
  <div class="abs service-label">АВИАБИЛЕТИ</div>

  <ol class="abs steps">
    <li class="step active" style="width:124px;padding-left:9px"><b>1</b>ВВОД ДАННЫХ
      <svg width="12" height="34" viewBox="0 0 12 34"><path d="M0 0 L6 0 L12 17 L6 34 L0 34 Z" fill="#6b2310"/><path d="M4 3 L10 17 L4 31" stroke="#f1e6d6" fill="none"/></svg></li>
    <li class="step" style="width:128px;padding-left:16px"><b>2</b>ОБЗОР ТУРА
      <svg width="12" height="34" viewBox="0 0 12 34"><path d="M4 3 L10 17 L4 31" stroke="#f1e6d6" fill="none"/></svg></li>
    <li class="step" style="width:124px;padding-left:17px"><b>3</b>ОПЛАТА
      <svg width="12" height="34" viewBox="0 0 12 34"><path d="M4 3 L10 17 L4 31" stroke="#f1e6d6" fill="none"/></svg></li>
    <li class="step" style="width:213px;padding-left:17px"><b>4</b>ПОДТВЕРЖДЕНИЕ ЗАКАЗА</li>
  </ol>

  <section class="abs leg" style="left:154px;top:474px">
    <h3>Туда</h3>
    <p>Рейс: Northfield (NFD) → Karsel Intl (KRL)</p>
    <p>Продолжительность перелета: 2ч50м</p>
    <div class="carrier"><i></i>KORVEL AIR</div>
    <dl><dt>Номер рейса:</dt><dd>KV2180</dd><dt>Вылет:</dt><dd>14:40, 22 Июнь 2013</dd><dt>Прилет:</dt><dd>18:30, 22 Июнь 2013</dd></dl>
  </section>

  <section class="abs leg" style="left:512px;top:474px">
    <h3>Обратно</h3>
    <p>Рейс: Karsel Intl (KRL) → Northfield (NFD)</p>
    <p>Продолжительность перелета: 3ч00м</p>
    <div class="carrier"><i></i>KORVEL AIR</div>
    <dl><dt>Номер рейса:</dt><dd>KV2181</dd><dt>Вылет:</dt><dd>10:40, 02 Июль 2013</dd><dt>Прилет:</dt><dd>12:40, 02 Июль 2013</dd></dl>
  </section>

  <p class="abs terms">УСЛОВИЯ ВОЗВРАТА И ОБМЕНА БИЛЕТОВ &nbsp;-&nbsp; подробнее</p>
  <div class="abs price-tag">20862 Руб</div>

  <form>
    <label class="abs field-label" style="left:155px;top:699px">Имя</label>
    <div class="abs field" style="left:154px;top:722px;width:193px"></div>
    <label class="abs field-label" style="left:365px;top:699px">Фамилия</label>
    <div class="abs field" style="left:363px;top:722px;width:193px"></div>
    <label class="abs field-label" style="left:573px;top:699px">Дата рождения</label>
    <div class="abs field" style="left:571px;top:722px;width:193px"></div>
    <label class="abs field-label" style="left:782px;top:699px">Пол</label>
    <div class="abs field" style="left:780px;top:722px;width:97px"><span class="select-arrow"><svg width="8" height="5"><path d="M0 0 L8 0 L4 5 Z" fill="#2b140a"/></svg></span></div>

    <label class="abs field-label" style="left:156px;top:767px">Номер Документа</label>
    <div class="abs field" style="left:154px;top:786px;width:193px"></div>
    <label class="abs field-label" style="left:365px;top:767px">Страна выдачи</label>
    <div class="abs field" style="left:363px;top:786px;width:193px"><span class="select-arrow"><svg width="8" height="5"><path d="M0 0 L8 0 L4 5 Z" fill="#2b140a"/></svg></span></div>
    <label class="abs field-label" style="left:573px;top:767px">Годен до</label>
    <div class="abs field" style="left:571px;top:786px;width:193px"></div>
    <div class="abs nodate">Без даты <span class="tick"><svg width="9" height="7"><path d="M1 3.5 L3.5 6 L8 1" stroke="#fff" stroke-width="1.6" fill="none"/></svg></span></div>
  </form>

  <a class="abs nav-btn" style="left:157px">НАЗАД</a>
  <div class="abs total">Итоговая сумма: 20862 Руб</div>
  <a class="abs nav-btn" style="right:147px">ПРОДОЛЖИТЬ</a>
</main>

<footer>
  <div class="abs old-map" role="img" aria-label="Old paper map of Europe, slightly rotated"></div>

  <div class="abs foot-col" style="left:122px;top:1003px">
    <h4>ПРОСМОТР САЙТА</h4>
    <ul><li>Домой</li><li>О нас</li><li>Форум</li><li>Контакты</li></ul>
  </div>
  <div class="abs foot-col" style="left:298px;top:1001px">
    <h4>ПОМОЩЬ</h4>
    <ul><li>Помощь</li><li>Правила пользования</li><li>Политика конфиденциальности</li><li>Cookies</li></ul>
  </div>
  <div class="abs foot-col" style="left:503px;top:1003px">
    <h4>НАЙТИ НАС</h4>
    <ul><li>Sunkettle Limited</li><li>14 Harrow Lane</li><li>London, N4 2QR</li><li>UK</li></ul>
  </div>
  <div class="abs foot-col" style="left:674px;top:1003px">
    <h4>МЫ В</h4>
  </div>
  <div class="abs social"><span></span><span></span><span></span></div>

  <ul class="abs contacts">
    <li><svg viewBox="0 0 12 12"><path d="M1 4 Q6 0 11 4 L10 6 L8 5 L8 3.5 Q6 3 4 3.5 L4 5 L2 6 Z M3 6.5 L9 6.5 L11 11 L1 11 Z" fill="#2b140a"/></svg>+7 (495) 555-01-87</li>
    <li><svg viewBox="0 0 12 12"><rect x="0.5" y="2.5" width="11" height="7" fill="none" stroke="#2b140a"/><path d="M0.5 2.5 L6 7 L11.5 2.5" fill="none" stroke="#2b140a"/></svg>info@sunkettle.com</li>
    <li><svg viewBox="0 0 12 12"><circle cx="2" cy="10" r="1.5" fill="#2b140a"/><path d="M1 5.5 A5.5 5.5 0 0 1 6.5 11 M1 1.5 A9.5 9.5 0 0 1 10.5 11" fill="none" stroke="#2b140a" stroke-width="1.6"/></svg>Экслюзивные предложения</li>
  </ul>
  <div class="abs mail-form"><div class="mail">E- mail</div><div class="send">Отправить</div></div>

  <p class="abs copyright">2013 © Sunkettle.com</p>
</footer>

</body>
</html>
```